Corvel Capital LLC

Need Professional Business cards for New Investment Fund

Target Market(s)

High Quality investors

Industry/Entity Type

Financial

Contact Information for Business Card

Phone Number +1 555 284 6190
Name Lukas Varenko
Title Fund Manager
email lv@FundCorvel.com
Website www.FundCorvel.com

Colors

Designer to choose colors to be used in the design.

Requirements
Must have
• Must have our Logo and all of the above. Must be made so lettering and loge can be raised

```html
<!DOCTYPE html>
<html lang="en">
<head>
<meta charset="utf-8">
<title>Fund Manager Business Cards</title>
<link href="https://fonts.googleapis.com/css2?family=Arimo:wght@400;700&display=swap" rel="stylesheet">
<style>
  :root {
    --backdrop: #2a2d31;
    --brand-green: #5cbc45;
    --brand-green-light: #66c64e;
    --charcoal: #3a3d3b;
    --paper: #ffffff;
    --ink-light: #ffffff;
  }
  * { box-sizing: border-box; margin: 0; padding: 0; }
  html, body {
    width: 1200px; height: 900px; overflow: hidden;
    background: var(--backdrop);
    font-family: "Arimo", Arial, sans-serif;
  }
  .canvas {
    position: relative; width: 1200px; height: 900px;
    display: flex; align-items: center; justify-content: center; gap: 60px;
  }
  .card {
    position: relative; width: 525px; height: 300px; overflow: hidden;
    box-shadow: 0 12px 30px rgba(0,0,0,.45);
  }
  /* Front */
  .card-front { background: var(--paper); }
  .front-shape { position: absolute; inset: 0; width: 100%; height: 100%; }
  .wordmark {
    position: absolute; display: flex; align-items: center; gap: 10px;
    font-weight: 700; letter-spacing: 3px; white-space: nowrap;
  }
  .wordmark-mark { width: 18px; height: 18px; flex: none; }
  .card-front .wordmark { left: 40px; top: 72px; font-size: 24px; color: var(--charcoal); }
  .card-front .wordmark-mark { background: var(--brand-green); }
  .contact {
    position: absolute; left: 285px; top: 62px; color: var(--ink-light);
  }
  .contact-name { font-size: 22px; font-weight: 700; }
  .contact-title { font-size: 14px; margin-top: 3px; margin-bottom: 18px; }
  .contact-list { list-style: none; }
  .contact-item {
    display: flex; align-items: center; gap: 10px;
    font-size: 16px; margin-bottom: 10px;
  }
  .contact-icon { width: 15px; height: 15px; flex: none; }
  /* Back */
  .card-back {
    background: var(--brand-green-light);
    display: flex; align-items: center; justify-content: center;
  }
  .card-back .wordmark { position: static; font-size: 38px; color: var(--ink-light); letter-spacing: 5px; }
  .card-back .wordmark-mark { width: 24px; height: 24px; background: var(--ink-light); }
</style>
</head>
<body>
<main class="canvas">
  <section class="card card-front" aria-label="Business card front">
    <svg class="front-shape" viewBox="0 0 525 300" preserveAspectRatio="none" aria-hidden="true">
      <path d="M292 0 C222 70 204 190 222 300 L525 300 L525 0 Z" fill="var(--charcoal)"/>
      <path d="M302 0 C234 72 216 190 234 300 L525 300 L525 0 Z" fill="var(--brand-green-light)"/>
    </svg>
    <div class="wordmark"><span class="wordmark-mark"></span>OSTREVAN</div>
    <div class="contact">
      <p class="contact-name">Lukas Varenko</p>
      <p class="contact-title">Fund Manager</p>
      <ul class="contact-list">
        <li class="contact-item">
          <svg class="contact-icon" viewBox="0 0 16 16" aria-hidden="true"><path d="M4 1 L6.5 4.5 L5 6.5 Q6.5 9.5 9.5 11 L11.5 9.5 L15 12 L13 15 Q5 14 1 3 Z" fill="#fff"/></svg>
          +1 555 284 6190
        </li>
        <li class="contact-item">
          <svg class="contact-icon" viewBox="0 0 16 16" aria-hidden="true"><rect x="1" y="3" width="14" height="10" fill="#fff"/><path d="M1 3 L8 9 L15 3" fill="none" stroke="var(--brand-green-light)" stroke-width="1.5"/></svg>
          lv@FundCorvel.com
        </li>
        <li class="contact-item">
          <svg class="contact-icon" viewBox="0 0 16 16" aria-hidden="true"><circle cx="8" cy="8" r="7" fill="#fff"/><path d="M1 8 H15 M8 1 Q4 8 8 15 M8 1 Q12 8 8 15" fill="none" stroke="var(--brand-green-light)" stroke-width="1.2"/></svg>
          www.FundCorvel.com
        </li>
      </ul>
    </div>
  </section>
  <section class="card card-back" aria-label="Business card back">
    <div class="wordmark"><span class="wordmark-mark"></span>OSTREVAN</div>
  </section>
</main>
</body>
</html>
```